birchwell hollow cattle company website

we would like a home page, an about us page, a page for sires, a page for dams, A sale page where we can list progreny for sale and a contact us. on the about us page we would like there to be a family picture. on the sires page we would like to have a picture of each sire, a description beside them and a link to their online profile at northern hereford registry. on the dam page we would like to have a picture of each dam, aswell as a description beside them aswell as a link to the northern hereford registry site. would like the website to very mobile phone friendly as expecting most traffic to be on phone. we would like the website to look and feel very mich like a farm, rustic, barbed wire and other farm feels. we would also like a frozen genetics pages where we can include pictures and descriptions of the sires and dams aswell as a price for embryos and semen. we need to website to be easy to maintain so we can update pictures and information as it changes, we would like there to be a feature so that people can sign up to be on our mailing list by giving us their mailing addess and email and full name
aswell as an area where they can send us a message to contact us.

leaving for work for 3 weeks in the canadian arctic will have limited ability to use the internet

Target Market(s)

other ranchers, farmers, cattlemen,

Industry/Entity Type

farming, agriculture, cattle

Coding

Coded - Design and coding required

Requirements
Must have
• about page, contact page, sires page, dams page, SALE page.
Nice to have
• country/farm vibe, barbed wire, wood,

```html
<!DOCTYPE html>
<html lang="en">
<head>
<meta charset="utf-8">
<title>Birchwell Hollow Cattle Company</title>
<link rel="stylesheet" href="https://fonts.googleapis.com/css2?family=Bebas+Neue&family=Montserrat:wght@400;500;600&display=swap">
<style>
:root{
  --charcoal:#333232;
  --cream:#f4efe8;
  --sand:#e8dfd4;
  --brown:#8b5a35;
  --ink:#1e1e1e;
  --grey:#6a6560;
  --white:#ffffff;
}
*{box-sizing:border-box;margin:0;padding:0}
html,body{width:1200px;height:3883px;overflow:hidden}
body{font-family:"Montserrat",sans-serif;color:var(--ink);background:var(--cream);position:relative}
a{text-decoration:none}
.section{position:absolute;left:0;width:1200px}
.abs{position:absolute}
h1,h2{font-family:"Bebas Neue",sans-serif;font-weight:400;color:var(--charcoal);letter-spacing:.5px}
h2{font-size:40px;line-height:1}
.center{text-align:center;left:0;width:1200px}
.btn{position:absolute;display:flex;align-items:center;justify-content:center;background:var(--brown);color:var(--white);border-radius:20px;font-size:16px;font-weight:500}
.lead{font-size:15px;font-weight:500;line-height:26px;color:var(--ink)}
.body{font-size:15px;line-height:25.6px;color:var(--grey)}
.rule{position:absolute;height:3px;background:var(--brown);border-radius:2px}

/* header */
.site-header{top:0;height:94px;background:var(--charcoal);z-index:5}
.brand-badge{position:absolute;left:108px;top:0;width:182px;height:136px;background:var(--charcoal);border-radius:0 0 91px 91px;display:flex;flex-direction:column;align-items:center;justify-content:flex-end;padding-bottom:26px;color:var(--white);z-index:6}
.brand-badge .name{font-family:"Bebas Neue",sans-serif;font-size:26px;line-height:1}
.brand-badge .sub{font-family:"Bebas Neue",sans-serif;font-size:12px;letter-spacing:3px;margin-top:4px}
.brand-badge .dot{width:10px;height:10px;border-radius:50%;background:var(--white);margin-bottom:10px}
.nav a{position:absolute;top:36px;color:var(--white);font-size:16px}
.nav a.active{font-weight:600;border-bottom:2px solid var(--white);padding-bottom:2px}
.nav .contact{top:29px;left:960px;width:128px;height:36px;border-radius:18px;background:var(--brown);display:flex;align-items:center;justify-content:center;font-weight:500}

/* hero */
.hero{top:94px;height:557px;background:linear-gradient(180deg,#caa06a 0%,#b88a55 30%,#8a6a44 60%,#5b4a33 100%)}
.hero-photo{position:absolute;inset:0;background:
  radial-gradient(ellipse 420px 360px at 880px 320px,#9a6a40 0%,rgba(154,106,64,0) 70%),
  linear-gradient(90deg,rgba(60,48,36,.55) 0%,rgba(60,48,36,.1) 55%,rgba(0,0,0,0) 100%)}
.hero h1{position:absolute;left:110px;top:150px;font-size:52px;line-height:57px;color:var(--white)}
.hero p{position:absolute;left:112px;top:277px;width:520px;color:var(--white);font-size:15.5px;line-height:24px;font-weight:500}
.hero .btn-light{position:absolute;left:113px;top:342px;width:146px;height:34px;border-radius:17px;background:var(--white);color:var(--ink);font-size:16px;display:flex;align-items:center;justify-content:center}
.hero-band{position:absolute;left:0;bottom:0;width:1200px;height:8px;background:#2b2624}

/* welcome */
.welcome{top:651px;height:502px;background:var(--cream)}
/* sires */
.sires{top:1153px;height:692px;background:var(--sand)}
.card{position:absolute;top:261px;width:226px;height:345px;border:1.5px solid var(--brown);border-radius:14px;text-align:center}
.card .photo{position:absolute;left:15px;top:19px;width:196px;height:160px;border-radius:12px}
.card h3{position:absolute;top:199px;left:0;width:100%;font-size:16px;font-weight:500;color:var(--ink)}
.card p{position:absolute;top:228px;left:14px;width:198px;font-size:12.5px;line-height:19.5px;color:var(--grey)}
.card a{position:absolute;top:305px;left:0;width:100%;font-size:16px;font-weight:500;color:var(--brown);text-decoration:underline}
/* quality */
.quality{top:1845px;height:718px;background:var(--cream)}
.herd-photo{position:absolute;left:0;top:380px;width:1200px;height:338px;background:linear-gradient(180deg,rgba(244,239,232,1) 0%,rgba(160,170,175,.6) 14%,#2a2624 32%,#1f1c1a 70%,#7a6a45 88%,#9a8555 100%)}
/* frozen */
.frozen{top:2563px;height:527px;background:var(--sand)}
.frozen-art{position:absolute;left:663px;top:163px;width:445px;height:224px;border-radius:8px;background:#d9cec1}
/* newsletter */
.signup{top:3090px;height:438px;background:var(--cream)}
.field label{position:absolute;font-size:16px;color:var(--ink)}
.field .input{position:absolute;height:35px;border:1.5px solid #c9bfb3;border-radius:18px;font-size:10.5px;color:#9a938b;padding-left:20px;display:flex;align-items:center}
/* footer */
.site-footer{top:3528px;height:355px;background:var(--charcoal);color:var(--white)}
.footer-band{position:absolute;left:0;top:0;width:1200px;height:8px;background:#1a1817}
.footer-brand{position:absolute;left:0;width:1200px;top:108px;text-align:center}
.footer-brand .dot{width:14px;height:14px;border-radius:50%;background:var(--white);margin:0 auto 12px}
.footer-brand .name{font-family:"Bebas Neue",sans-serif;font-size:34px;line-height:1}
.footer-brand .sub{font-family:"Bebas Neue",sans-serif;font-size:15px;letter-spacing:5px;margin-top:4px}
.footer-nav a{position:absolute;top:266px;font-size:16px;color:var(--white);transform:translateX(-50%);white-space:nowrap}
.footer-rule{position:absolute;left:110px;top:301px;width:978px;height:1px;background:#6b6866}
.copyright{position:absolute;top:314px;left:0;width:1200px;text-align:center;font-size:12px}
</style>
</head>
<body>

<header class="section site-header">
  <div class="brand-badge"><span class="dot"></span><span class="name">Birchwell Hollow</span><span class="sub">Cattle Company</span></div>
  <nav class="nav">
    <a class="active" href="#" style="left:422px">Home</a>
    <a href="#" style="left:516px">About Us</a>
    <a href="#" style="left:630px">Sires</a>
    <a href="#" style="left:710px">Dams</a>
    <a href="#" style="left:799px">Sale</a>
    <a href="#" style="left:873px">More &#8964;</a>
    <a class="contact" href="#">Contact Us</a>
  </nav>
</header>

<section class="section hero">
  <div class="hero-photo" role="img" aria-label="Two cattle standing in tall grass at sunset"></div>
  <h1>Quality Angus Genetics<br>Raised Right</h1>
  <p>Family-run Angus operation focused on sound, practical cattle with strong maternal traits and real-world performance.</p>
  <a class="btn-light" href="#">Cattle for Sale</a>
  <div class="hero-band"></div>
</section>

<section class="section welcome">
  <h2 class="abs center" style="top:74px">Welcome to Birchwell Hollow</h2>
  <div class="rule" style="left:467px;top:128px;width:264px"></div>
  <p class="abs lead" style="left:180px;width:840px;top:171px;text-align:center">Lorem ipsum dolor sit amet, consectetur adipiscing elit, sed do eiusmod tempor incididunt ut labore et dolore magna aliqua. Quis ipsum suspendisse ultrices gravida.</p>
  <p class="abs body" style="left:100px;width:1000px;top:234px;text-align:center">Sed ut perspiciatis unde omnis iste natus error sit voluptatem accusantium doloremque laudantium,<br>totam rem aperiam, eaque ipsa quae ab illo inventore veritatis et quasi architecto beatae vitae dicta sunt explicabo.<br>Nemo enim ipsam voluptatem quia voluptas sit aspernatur aut odit aut fugit, sed quia consequuntur magni dolores<br>eos qui ratione voluptatem sequi nesciunt. Neque porro quisquam est, qui dolorem ipsum quia<br>dolor sit amet, consectetur, adipisci velit, sed quia non numquam</p>
  <a class="btn" href="#" style="left:535px;top:382px;width:130px;height:34px">Read More</a>
</section>

<section class="section sires">
  <h2 class="abs" style="left:110px;top:82px">Featured Sires</h2>
  <div class="rule" style="left:110px;top:133px;width:176px"></div>
  <p class="abs body" style="left:110px;top:174px;width:760px">Our herd sires are carefully selected for structural soundness, strong maternal influence, and<br>real-world performance.</p>
  <a class="btn" href="#" style="left:947px;top:186px;width:141px;height:34px">View All Sires</a>

  <article class="card" style="left:111px">
    <div class="photo" role="img" aria-label="Black Angus bull standing in green pasture" style="background:linear-gradient(180deg,#e8ecef 0%,#2a2828 45%,#232121 75%,#7fae3c 100%)"></div>
    <h3>BHC Granite 21K</h3>
    <p>Powerful, deep-bodied sire with strong maternal backing and excellent growth.</p>
    <a href="#">View Profile</a>
  </article>
  <article class="card" style="left:361px">
    <div class="photo" role="img" aria-label="Row of red and white cattle behind a wire fence" style="background:linear-gradient(180deg,#7b8f6a 0%,#8a4a2a 40%,#a0563a 65%,#6f8a4a 100%)"></div>
    <h3>BHC Timberline 14J</h3>
    <p>Smooth-made, structurally sound bull known for calving ease and consistent progeny.</p>
    <a href="#">View Profile</a>
  </article>
  <article class="card" style="left:611px">
    <div class="photo" role="img" aria-label="Close-up of a red-brown cattle hide" style="background:linear-gradient(135deg,#7a3e26 0%,#94543a 50%,#6e3520 100%)"></div>
    <h3>BHC Ironwood 8H</h3>
    <p>Performance-oriented sire with added muscle, length, and strong feed efficiency.</p>
    <a href="#">View Profile</a>
  </article>
  <article class="card" style="left:861px">
    <div class="photo" role="img" aria-label="Cattle grazing in a sunlit pasture" style="background:linear-gradient(180deg,#b7c3c6 0%,#8a9a6a 45%,#6e8a3c 75%,#8aa140 100%)"></div>
    <h3>BHC Blackridge 3L</h3>
    <p>Moderate-framed,<br>easy-fleshing bull with strong maternal genetics and quiet</p>
    <a href="#">View Profile</a>
  </article>
</section>

<section class="section quality">
  <h2 class="abs center" style="top:84px">Quality Cattle Available</h2>
  <div class="rule" style="left:513px;top:136px;width:174px"></div>
  <p class="abs lead" style="left:160px;width:880px;top:180px;text-align:center">Lorem ipsum dolor sit amet, consectetur adipiscing elit, sed do eiusmod tempor incididunt ut labore et dolore magna aliqua. Quis ipsum suspendisse ultrices gravida.</p>
  <p class="abs body" style="left:140px;width:920px;top:245px;text-align:center">Sed ut perspiciatis unde omnis iste natus error sit voluptatem accusantium doloremque laudantium, totam<br>rem aperiam, eaque ipsa quae ab illo inventore veritatis et quasi architecto beatae vitae dicta<br>sunt explicabo. Nemo enim ipsam voluptatem quia voluptas sit aspernatur aut odit aut fugit, sed quia<br>consequuntur magni dolores eos qui ratione voluptatem sequi nesciunt.</p>
  <div class="herd-photo" role="img" aria-label="Herd of black Angus cattle standing in a dry grass field"></div>
  <a class="btn" href="#" style="left:502px;top:367px;width:194px;height:34px">View Cattle for Sale</a>
</section>

<section class="section frozen">
  <h2 class="abs" style="left:109px;top:85px">Frozen Genetics</h2>
  <div class="rule" style="left:110px;top:136px;width:176px"></div>
  <p class="abs lead" style="left:110px;top:178px;width:502px;text-align:justify">Sed ut perspiciatis unde omnis iste natus error sit voluptatem accusantium doloremque laudantium, totam rem aperiam, eaque ipsa quae ab illo inventore veritatis et</p>
  <p class="abs body" style="left:110px;top:264px;width:502px">Lorem ipsum dolor sit amet, consectetur adipiscing elit, sed do eiusmod tempor incididunt ut labore et dolore magna aliqua. Ut enim ad minim veniam, quis nostrud exercitation ullamco laboris nisi ut aliquip ex ea commodo consequat. Duis aute irure dolor in reprehenderit in voluptate velit esse</p>
  <a class="btn" href="#" style="left:110px;top:407px;width:213px;height:34px">View Frozen Genetics</a>
  <div class="frozen-art" role="img" aria-label="Dark silhouette of a cow standing in grass"></div>
</section>

<section class="section signup">
  <h2 class="abs center" style="top:80px">Stay Updated with Birchwell Hollow</h2>
  <div class="rule" style="left:467px;top:134px;width:264px"></div>
  <p class="abs body" style="left:200px;width:800px;top:182px;text-align:center">Sed ut perspiciatis unde omnis iste natus error sit voluptatem accusantium doloremque laudantium,<br>totam rem aperiam, eaque ipsa quae ab illo inventore veritatis</p>
  <div class="field">
    <label style="left:111px;top:268px">Full Name</label>
    <div class="input" style="left:111px;top:302px;width:313px">Enter Your Name</div>
    <label style="left:444px;top:268px">Email Address</label>
    <div class="input" style="left:444px;top:302px;width:312px">Enter Your Email Address</div>
    <label style="left:776px;top:268px">Mailing Address</label>
    <div class="input" style="left:776px;top:302px;width:312px">Enter Your Mailing Address</div>
  </div>
  <a class="btn" href="#" style="left:525px;top:361px;width:150px;height:34px">Subscribe</a>
</section>

<footer class="section site-footer">
  <div class="footer-band"></div>
  <div class="footer-brand"><div class="dot"></div><div class="name">Birchwell Hollow</div><div class="sub">Cattle Company</div></div>
  <nav class="footer-nav">
    <a href="#" style="left:276px">Home</a>
    <a href="#" style="left:387px">About Us</a>
    <a href="#" style="left:492px">Sires</a>
    <a href="#" style="left:583px">Dams</a>
    <a href="#" style="left:671px">Sale</a>
    <a href="#" style="left:790px">Frozen Genetics</a>
    <a href="#" style="left:920px">Contact</a>
  </nav>
  <div class="footer-rule"></div>
  <p class="copyright">Copyright © 2026 Birchwell Hollow. All rights reserved.</p>
</footer>

</body>
</html>
```